Weightloss company needs Business Card

We want a business card that is clean and professional, yet portrays that we are a friendly, innovative, and versatile program designed to fit the needs of our clients.
I would like there to be 2 sides, one side having an appointment card, and the other side containing the logo and business information. There can be decorations on both sides. The logo is attached.

Target Market(s)

Men and women 40-60

Industry/Entity Type

Business

Contact Information for Business Card

Font styles to use
Sans Serif

Requirements
Must have
• The logo, space for business information
Nice to have
• The colors in the logo
Should not have
• No pictures of people or food

```html
<!DOCTYPE html>
<html lang="en">
<head>
<meta charset="utf-8">
<title>Renewal Turn – Business Card</title>
<link href="https://fonts.googleapis.com/css2?family=Didact+Gothic&display=swap" rel="stylesheet">
<style>
  :root {
    --brand-red: #e8203a;
    --brand-blue: #3fc1e8;
    --ink: #050505;
    --paper: #ffffff;
    --text-dark: #1a1a1a;
    --backdrop: #2e2e30;
    --rule: #333333;
  }
  * { margin: 0; padding: 0; box-sizing: border-box; }
  html, body {
    width: 1200px; height: 900px; overflow: hidden;
    background: var(--backdrop);
    font-family: "Didact Gothic", "Century Gothic", sans-serif;
  }
  .canvas { position: relative; width: 1200px; height: 900px; }
  .card {
    position: absolute; width: 640px; height: 366px;
    background: var(--paper); border-radius: 22px; overflow: hidden;
  }
  .card--appointment { left: 90px; top: 60px; }
  .card--contact { left: 470px; top: 474px; }

  .brand {
    position: absolute; top: 44px; right: 44px;
    display: flex; align-items: center; gap: 10px;
    color: var(--brand-red); font-size: 30px; letter-spacing: 0.5px;
  }
  .brand__dot {
    width: 16px; height: 16px; border-radius: 50%; background: var(--brand-red);
  }

  .appointment {
    position: absolute; left: 70px; top: 178px; width: 470px;
  }
  .appointment__title {
    color: var(--brand-red); font-size: 15px; letter-spacing: 0.5px; margin-bottom: 14px;
  }
  .appointment__field {
    display: flex; align-items: flex-end; gap: 10px;
    font-size: 17px; color: var(--text-dark); margin-bottom: 24px;
  }
  .appointment__line {
    flex: 1; border-bottom: 1.5px solid var(--rule); height: 1px; margin-bottom: 5px;
  }

  .contact-panel { position: absolute; left: 0; top: 0; }
  .contact {
    position: absolute; left: 140px; top: 140px; color: var(--paper);
  }
  .contact__name {
    color: var(--brand-blue); font-size: 30px; letter-spacing: 1px; line-height: 1.1;
  }
  .contact__role { font-size: 15px; letter-spacing: 0.5px; margin-bottom: 12px; }
  .contact__address { font-size: 16px; line-height: 1.3; margin-bottom: 8px; }
  .contact__row {
    display: flex; align-items: center; gap: 10px; font-size: 16px; line-height: 1.45;
  }
  .contact__icon { width: 14px; height: 14px; flex: none; }
</style>
</head>
<body>
<main class="canvas">

  <section class="card card--appointment">
    <div class="brand"><span class="brand__dot"></span>Renewal Turn</div>
    <div class="appointment">
      <p class="appointment__title">APPOINTMENT</p>
      <div class="appointment__field">Name:<span class="appointment__line"></span></div>
      <div class="appointment__field">Date:<span class="appointment__line"></span></div>
      <div class="appointment__field">Time:<span class="appointment__line"></span></div>
    </div>
  </section>

  <section class="card card--contact">
    <div class="brand"><span class="brand__dot"></span>Renewal Turn</div>
    <svg class="contact-panel" width="640" height="366" viewBox="0 0 640 366">
      <circle cx="250" cy="420" r="320" fill="var(--brand-blue)"/>
      <circle cx="250" cy="420" r="317" fill="var(--brand-red)"/>
      <circle cx="250" cy="420" r="302" fill="var(--brand-blue)"/>
      <circle cx="250" cy="420" r="300" fill="var(--ink)"/>
    </svg>
    <div class="contact">
      <p class="contact__name">MARCUS HALE</p>
      <p class="contact__role">DIRECTOR</p>
      <p class="contact__address">Harbor Lane, 40512<br>Westfield, Oakridge</p>
      <p class="contact__row">
        <svg class="contact__icon" viewBox="0 0 24 24"><path fill="var(--brand-blue)" d="M6.6 10.8a15.1 15.1 0 0 0 6.6 6.6l2.2-2.2c.3-.3.7-.4 1-.2 1.1.4 2.3.6 3.6.6.6 0 1 .4 1 1V20c0 .6-.4 1-1 1A17 17 0 0 1 3 4c0-.6.4-1 1-1h3.5c.6 0 1 .4 1 1 0 1.3.2 2.5.6 3.6.1.3 0 .7-.2 1z"/></svg>
        +330 5172-0384
      </p>
      <p class="contact__row">
        <svg class="contact__icon" viewBox="0 0 24 24"><rect x="2" y="5" width="20" height="14" rx="1.5" fill="none" stroke="var(--brand-blue)" stroke-width="2"/><path d="M2.5 6l9.5 7 9.5-7" fill="none" stroke="var(--brand-blue)" stroke-width="2"/></svg>
        hello@renewalturn.com
      </p>
      <p class="contact__row">
        <svg class="contact__icon" viewBox="0 0 24 24"><circle cx="12" cy="12" r="9.5" fill="none" stroke="var(--brand-blue)" stroke-width="2"/><path d="M2.5 12h19M12 2.5c3 3 3 16 0 19M12 2.5c-3 3-3 16 0 19" fill="none" stroke="var(--brand-blue)" stroke-width="1.6"/></svg>
        www.renewalturn.com
      </p>
    </div>
  </section>

</main>
</body>
</html>
```